Salon and Spa Distributor Business Card

Need a business card. We are are distributor in the salon and spa industry. We identify with natural beauty. Need a card with:
Company Name: Petal Quarry"
Title: "President & CEO"
Address
Company Phone number
email
website
Tag Line:" The Professional Salon Source"

Industry/Entity Type

Business

Contact Information for Business Card

Name: Dov Strommen
Title: "President & CEO"
Address: 31 Harlow Ln, Bexmoor, NJ 07813
Company Phone number: 800-463-5918
email: dovstrommen@petalquarry.example
website: www.petalquarry.example

Requirements
Should not have
• No black backgrounds

```html
<!DOCTYPE html>
<html lang="en">
<head>
<meta charset="utf-8">
<title>Petal Quarry Business Card</title>
<link rel="stylesheet" href="https://fonts.googleapis.com/css2?family=Courgette&family=Questrial&family=Open+Sans:wght@700&family=Lora:ital@1&display=swap">
<style>
  :root {
    --green: #4caf3a;
    --green-deep: #2f7f22;
    --green-dark: #1f6a1a;
    --green-light: #6cc24a;
    --paper: #ffffff;
    --ink: #333333;
    --backdrop: #e9ece8;
  }
  * { margin: 0; padding: 0; box-sizing: border-box; }
  html, body { width: 1200px; height: 997px; overflow: hidden; }
  body { background: var(--backdrop); position: relative; font-family: "Questrial", sans-serif; }

  .card {
    position: absolute; width: 530px; height: 303px;
    border-radius: 14px; overflow: hidden;
    box-shadow: 0 12px 30px rgba(0,0,0,.18);
  }
  /* front */
  .card-front { left: 60px; top: 190px; background: linear-gradient(135deg, var(--green-light), var(--green-deep)); }
  .front-art {
    position: absolute; left: 40px; top: 40px; width: 260px; height: 230px;
    border-radius: 50% 45% 40% 50%;
    background: radial-gradient(ellipse at 55% 45%, rgba(255,255,255,.85), rgba(255,255,255,.35) 70%, rgba(255,255,255,0));
  }
  .tagline {
    position: absolute; right: 60px; top: 38px; width: 170px;
    font-family: "Courgette", cursive; font-size: 24px; line-height: 1.3;
    color: var(--paper); text-align: center;
  }

  /* back */
  .card-back { left: 610px; top: 500px; background: var(--paper); }
  .back-band { position: absolute; inset: 0; }
  .holder { position: absolute; right: 26px; top: 16px; text-align: right; color: var(--paper); }
  .holder-name { font-family: "Open Sans", sans-serif; font-weight: 700; font-size: 17px; }
  .holder-title { font-family: "Lora", serif; font-style: italic; font-size: 13px; }

  .brand { position: absolute; left: 30px; top: 125px; display: flex; align-items: center; gap: 14px; }
  .brand-mark { width: 50px; height: 50px; border-radius: 50%; background: var(--green); }
  .brand-name { font-size: 30px; color: var(--green); }

  .contacts { position: absolute; left: 30px; bottom: 22px; list-style: none; }
  .contact { display: flex; align-items: center; gap: 10px; font-size: 15px; color: var(--ink); margin-top: 8px; }
  .contact-icon { width: 22px; height: 22px; border-radius: 50%; background: var(--green-deep); display: flex; align-items: center; justify-content: center; }
  .contact-icon svg { width: 12px; height: 12px; fill: var(--paper); }

  .website {
    position: absolute; right: 26px; bottom: 100px;
    font-family: "Open Sans", sans-serif; font-weight: 700; font-size: 17px; color: var(--green-dark);
  }
</style>
</head>
<body>
  <section class="card card-front">
    <div class="front-art" role="img" aria-label="White illustration of a woman's profile with flowing hair and leaves"></div>
    <p class="tagline">The Professional Salon Source</p>
  </section>

  <section class="card card-back">
    <svg class="back-band" viewBox="0 0 530 303" preserveAspectRatio="none" aria-hidden="true">
      <path d="M0 0 H530 V120 Q330 30 0 80 Z" fill="var(--green)"/>
      <path d="M0 92 Q330 44 530 140" fill="none" stroke="var(--green-deep)" stroke-width="7"/>
    </svg>
    <div class="holder">
      <p class="holder-name">Dov Strommen</p>
      <p class="holder-title">President &amp; CEO</p>
    </div>
    <div class="brand">
      <span class="brand-mark"></span>
      <span class="brand-name">Petal Quarry</span>
    </div>
    <ul class="contacts">
      <li class="contact">
        <span class="contact-icon"><svg viewBox="0 0 24 24"><path d="M6.6 10.8a15 15 0 0 0 6.6 6.6l2.2-2.2a1 1 0 0 1 1-.25 11.4 11.4 0 0 0 3.6.57 1 1 0 0 1 1 1V20a1 1 0 0 1-1 1A17 17 0 0 1 3 4a1 1 0 0 1 1-1h3.5a1 1 0 0 1 1 1c0 1.25.2 2.45.57 3.57a1 1 0 0 1-.25 1z"/></svg></span>
        800-463-5918
      </li>
      <li class="contact">
        <span class="contact-icon"><svg viewBox="0 0 24 24"><path d="M2 5h20v14H2z M2 5l10 8 10-8" /></svg></span>
        dovstrommen@petalquarry.example
      </li>
      <li class="contact">
        <span class="contact-icon"><svg viewBox="0 0 24 24"><path d="M12 2a7 7 0 0 0-7 7c0 5 7 13 7 13s7-8 7-13a7 7 0 0 0-7-7zm0 9.5A2.5 2.5 0 1 1 12 6.5a2.5 2.5 0 0 1 0 5z"/></svg></span>
        31 Harlow Ln, Bexmoor, NJ 07813
      </li>
    </ul>
    <p class="website">www.petalquarry.example</p>
  </section>
</body>
</html>
```